A unique communication angle to crowdfunding

Looking for a fresh redesign of a crowd funding website that deals in real estate. I already have the content, but am looking to take the design to the next level.

Existing real estate crowd funding sites focus on the real estate. I want to explore communication angle that:
- puts the investor in the centre of the communication: "become a baron"
- highlights the international nature (international properties, international investors)

There's also quite a lot of copy on the site, as we need to explain the service in quite a bit of detail. There's room to reduce the copy and replace with graphics. Could also consider clicking to see different text (see our difference section in http://galleonfairs.com)

The backend of the platform is already being worked on by a specialist crowd funding service provider.

In total there are 5 pages to be designed.

The homepage is really important. Right now it looks quite dated. It doesn't have a great layout. Note there is no mobile version of the website, so the pages need to be seen well on mobile devices. When looking at the brief, refer to the following links too:

current website:
http://pennyduke.com

some revisions made so far:
http://preview.stakeharbor.com/7K3LQ9

Attached are logo files and another file which contained copy for the pages. No need to rework the logo.

Please make sure to use the same copy in the brief on the webpages, to ensure the layouts work. Designers are free to propose images they feel work on the pages.

I would like to see if rather than tweaking the pages, it's possible to come up with a better design concept. If the 5 pages are accepted, there's a chance I'll request an additional 4 pages.
Updates

Please note the font used in the logo is called "harabara" in case you decide to use it in any of the titles, etc.

Please note there is one additional page for which we would like to review designs. Note the page would be a template to be used on all future real estate detail pages. Here is an example of the current design for reference:

http://pennyduke.com/projects/view/14

In total there are 5 page designs required, (homepage + 4)

Thank you

FYI -

Just a quick note to give information from similar UK real estate crowdfunding sites:
http://www.housewalrus.co.uk
http://tiderock.co.uk
https://www.fundquarry.com

Of the above, only tiderock has a nice clean looking landing page. Information is clear and well laid out.

Hi all, just uploaded a new file in the brief. Contains some comments and a website reference. I thought it may help to explain how we could convey international aspect as well as how we could convey images in a more modern way. This is an option you can consider, but its entirely up to you how how answer the brief. Thanks!

Reason: As requested by some designers needing more time to complete their work. Continue to share your work in progress and receive timely feedback before the deadline.

We would like to let you know that we have just shortlisted the best designs. Together with that, we have also passed some detailed feedback to all designers who weren't shortlisted. If we didn't contact you, please let us know. If you haven't submitted a design or are working on revisions, please note these will no longer be taken into account now. We hope you understand that we need to close the project today. Thank you all once again for your great work and design concepts. Here's hoping we meet again on a future design brief. Cheers, pennyduke team.

Target Market(s)

At the moment, only rich are able to buy real estate. With this service, anyone can become a landlord. Target buyers:

Young professionals, looking to diversify from stock market and lower risk
People nearing retirement, looking for stable rental incomes
Retirees - looking to supplement pensions with possibility of capital gains
Parents - looking for a way to save long term for their children (instead of low interest paying bank accounts)

Industry/Entity Type

Communication

Font styles to use
Sans Serif
Other font styles liked:
• harabara

Colors
add136
f5f9eb
959595
000000

Requirements
Must have
• Overall, the site must convey "whoever you are, you too can become a landlord", and that you don't need to be wealthy to invest in real estate. See

Communication should put the investor (or the baron) at the centre. The investor can be any of those described in the target market.

Show the aspirational side of property ownership.

In addition to the investor/baron character, the second main theme is international. No other real estate crowdfunding website highlights this.
Nice to have
• Banner could show different consumer types, to illustrate that the service can appeal to many different profiles. Refer to attached file "home page reference - plainasbread.com" as an example of how this could be done.

Aim to show the international side of the service. Properties around the world, investors around the world.

```html
<!DOCTYPE html>
<html lang="en">
<head>
<meta charset="utf-8">
<title>pennyduke – Social real estate investment</title>
<link href="https://fonts.googleapis.com/css2?family=Open+Sans:wght@400;600;700&family=Nunito:wght@700;800&display=swap" rel="stylesheet">
<style>
:root{
  --green:#8cc63f;
  --green-dark:#74a92c;
  --green-soft:#f5f9eb;
  --ink:#333333;
  --grey:#959595;
  --grey-light:#f3f3f3;
  --line:#dddddd;
  --badge:#bcbcbc;
  --white:#ffffff;
}
*{box-sizing:border-box;margin:0;padding:0}
html,body{width:1200px;height:3000px;overflow:hidden;background:var(--white)}
body{position:relative;font-family:"Open Sans",Arial,sans-serif;color:var(--ink);font-size:14px}
.heading{font-family:"Nunito","Open Sans",sans-serif;color:var(--green);font-weight:800}

/* header */
.site-header{position:absolute;left:0;top:0;width:1200px;height:96px;background:var(--white)}
.brand{position:absolute;left:154px;top:24px;display:flex;align-items:center;gap:10px}
.brand-dot{width:40px;height:40px;border-radius:50%;background:var(--green)}
.brand-name{font-size:26px;font-weight:600;color:var(--green)}
.follow{position:absolute;left:618px;top:20px;display:flex;align-items:center;gap:8px;font-size:13px;color:#555}
.social{width:36px;height:28px;display:flex;align-items:center;justify-content:center}
.social.solid{background:var(--green)}
.search{position:absolute;left:808px;top:20px;width:246px;height:30px;display:flex}
.search-field{flex:1;background:#ececec;font-size:11px;color:#999;padding:8px 10px}
.search-btn{width:36px;background:#555;position:relative}
.search-btn svg{position:absolute;left:10px;top:7px}
.main-nav{position:absolute;right:144px;top:68px;display:flex;gap:30px;font-size:11px;color:#555;text-transform:uppercase}
.main-nav .current{color:#222;font-weight:700;border-bottom:2px solid #222;padding-bottom:2px}

/* hero */
.hero{position:absolute;left:0;top:96px;width:1200px;height:388px;overflow:hidden;background:#e4e4e4}
.hero-photo{position:absolute;inset:0;background:linear-gradient(180deg,rgba(120,120,120,.55) 0%,rgba(190,190,190,.35) 55%,rgba(238,238,238,0) 85%),linear-gradient(90deg,#8a8a8a 0%,#b5b5b5 12%,#9c9c9c 22%,#cfcfcf 34%,#a9a9a9 48%,#d8d8d8 60%,#b2b2b2 72%,#c6c6c6 84%,#a0a0a0 100%)}
.hero-art{position:absolute;left:740px;top:48px;width:270px;height:306px;border-radius:12px;background:linear-gradient(160deg,#d9eebc 0%,#a6d464 40%,#7eb43a 70%,#e8d28a 100%)}
.hero-caption{position:absolute;left:186px;top:156px;width:502px;height:82px;background:var(--green);padding:12px 18px}
.hero-caption h1{font-size:23px;font-weight:700;color:#111;margin-bottom:6px}
.hero-caption p{font-size:13px;color:#fff}
.hero-arrow{position:absolute;top:168px;width:44px;height:44px;border-radius:50%;background:#3b3b3b;border:2px solid #888}
.hero-arrow svg{position:absolute;left:12px;top:11px}
.hero-dots{position:absolute;left:130px;top:368px;display:flex;gap:6px}
.hero-dots span{width:10px;height:10px;border-radius:50%;background:#444}
.hero-dots span.on{background:var(--green)}
.hero-shadow{position:absolute;left:100px;top:484px;width:1000px;height:12px;background:radial-gradient(ellipse at top,rgba(0,0,0,.25),rgba(0,0,0,0) 70%)}

/* intro */
.intro{position:absolute;left:0;top:496px;width:1200px;text-align:center}
.intro h2{font-size:28px;margin-top:34px}
.intro .rule{width:470px;height:2px;background:#e3e3e3;margin:12px auto 22px}
.intro p{font-size:13.5px;line-height:22px;color:#555;margin-bottom:22px}
.accent{color:var(--green);font-weight:600}

/* join */
.join{position:absolute;left:0;top:786px;width:1200px;height:306px;background:var(--grey-light)}
.join-card{position:absolute;top:52px;width:368px;height:146px;background:var(--white);border:1px solid var(--line);padding:26px 20px 0 116px}
.join-card .icon{position:absolute;left:18px;top:24px;width:78px;height:78px;border-radius:50%;background:#555}
.join-card .icon svg{position:absolute;left:19px;top:19px}
.join-card h3{font-size:21px;margin-bottom:4px}
.join-card p{font-size:13px;line-height:22px;color:#555}
.join-btn{position:absolute;top:210px;width:368px;height:46px;background:var(--green);border-bottom:3px solid var(--green-dark);color:#fff;font-family:"Nunito",sans-serif;font-weight:800;font-size:20px;text-align:center;line-height:44px}

/* projects */
.projects{position:absolute;left:0;top:1092px;width:1200px;height:622px;text-align:center}
.projects h2{font-size:22px;margin-top:20px}
.projects .lead{font-size:13px;line-height:24px;color:#555;margin-top:10px}
.project{position:absolute;top:144px;width:292px;height:416px;border:1px solid var(--line);background:#fff;text-align:left}
.project.raised{box-shadow:0 3px 8px rgba(0,0,0,.25)}
.project-photo{position:relative;height:206px;background:linear-gradient(180deg,#6aa7e0 0%,#9cc4ea 38%,#b07a5c 56%,#8d5a44 68%,#7a9d58 86%,#9a9a8a 100%)}
.price-tag{position:absolute;left:0;top:0;background:var(--green);color:#fff;font-size:11px;font-weight:700;padding:4px 8px}
.launch-tag{position:absolute;left:0;top:30px;background:#6b6b6b;color:#e5f4c9;font-size:10px;padding:3px 8px}
.project h3{font-size:15px;font-weight:600;color:var(--green);padding:12px 10px 0}
.project .summary{border-top:1px solid var(--line);margin:10px 10px 0;padding-top:8px;font-size:12px;line-height:20px;color:#444}
.funded{border-top:1px solid var(--line);margin:14px 10px 0;padding-top:8px;font-size:13px;font-weight:700;color:#444}
.bar{margin-top:6px;width:270px;height:16px;border:1px solid #bbb;background:#f7f7f7;position:relative}
.bar-fill{height:100%;background:var(--green)}
.bar-label{position:absolute;top:0;font-size:11px;font-weight:700;color:#222;line-height:14px}
.detail-link{text-align:center;font-size:13px;font-weight:600;color:#555;margin-top:10px}
.detail-link.active{color:var(--green)}

/* community */
.community{position:absolute;left:0;top:1714px;width:1200px;height:422px;background:linear-gradient(180deg,#4a4a4a 0%,#2f2f2f 55%,#1c1c1c 100%);text-align:center}
.community h2{font-size:22px;margin-top:54px}
.community .lead{font-size:14px;line-height:24px;color:#9a9a9a;width:660px;margin:10px auto 0}
.stat{position:absolute;top:212px;width:260px;text-align:center}
.stat .figure{font-family:"Nunito",sans-serif;font-weight:800;color:var(--green);font-size:21px;line-height:26px;height:60px;display:flex;align-items:center;justify-content:center}
.stat p{font-size:14px;line-height:24px;color:#ddd;margin-top:14px}
.stat .pin{position:absolute}

/* featured in */
.press{position:absolute;left:144px;top:2196px;width:912px;height:192px;border:1px solid var(--line);background:#fff}
.press-label{position:absolute;left:378px;top:-18px;width:174px;height:40px;background:var(--green);color:#fff;font-size:15px;font-weight:600;text-align:center;line-height:40px;border-bottom:3px solid var(--green-dark)}
.press-row{position:absolute;display:flex;align-items:center}
.press-badge{background:var(--badge);border-radius:2px}

/* skyline + footer */
.skyline{position:absolute;left:0;top:2400px;width:1200px;height:140px;background:linear-gradient(180deg,#ffffff 0%,#d8d8d8 45%,#a6a6a6 100%)}
.footer-bar{position:absolute;left:0;top:2540px;width:1200px;height:64px;background:#3a3a3a}
.footer-follow{position:absolute;left:144px;top:16px;display:flex;align-items:center;gap:12px;color:var(--green);font-size:17px;font-weight:600}
.footer-sq{width:38px;height:32px;border:2px solid var(--green);display:flex;align-items:center;justify-content:center}
.copyright{position:absolute;right:144px;top:22px;color:var(--green);font-size:13px}
.legal{position:absolute;left:0;top:2604px;width:1200px;height:396px;background:#f5f5f5}
.legal p{position:absolute;left:144px;font-size:12.5px;line-height:22px;color:#555;width:912px}
.group-name{position:absolute;left:842px;top:2626px;font-size:34px;color:#333;line-height:40px}
</style>
</head>
<body>

<header class="site-header">
  <div class="brand"><span class="brand-dot"></span><span class="brand-name">pennyduke</span></div>
  <div class="follow">Follow us on
    <span class="social solid"><svg width="16" height="16" viewBox="0 0 16 16"><circle cx="4" cy="8" r="2.2" fill="#fff"/><circle cx="12" cy="3.5" r="2.2" fill="#fff"/><circle cx="12" cy="12.5" r="2.2" fill="#fff"/><path d="M4 8 L12 3.5 M4 8 L12 12.5" stroke="#fff" stroke-width="1.4"/></svg></span>
    <span class="social"><svg width="16" height="14" viewBox="0 0 16 14"><path d="M1 1h14v9H6l-4 3v-3H1z" fill="#555"/></svg></span>
  </div>
  <div class="search">
    <div class="search-field">Search...</div>
    <div class="search-btn"><svg width="16" height="16" viewBox="0 0 16 16"><circle cx="6.5" cy="6.5" r="4.5" fill="none" stroke="#fff" stroke-width="2"/><line x1="10" y1="10" x2="14" y2="14" stroke="#fff" stroke-width="2"/></svg></div>
  </div>
  <nav class="main-nav">
    <span class="current">Home</span><span>Sign in</span><span>How it works</span><span>Discover a project</span><span>The baron blog</span><span>Find out more</span>
  </nav>
</header>

<section class="hero">
  <div class="hero-photo" role="img" aria-label="Grey city skyline of tall office towers"></div>
  <div class="hero-art" role="img" aria-label="Illustration of a green-roofed house with a shield, key and stacks of gold coins"></div>
  <div class="hero-caption">
    <h1>One property at a time</h1>
    <p>Invest from 1% in a property. Diversify across cities and properties.</p>
  </div>
  <div class="hero-arrow" style="left:92px"><svg width="16" height="18" viewBox="0 0 16 18"><path d="M11 2 L4 9 L11 16" fill="none" stroke="#8cc63f" stroke-width="3"/></svg></div>
  <div class="hero-arrow" style="left:1062px"><svg width="16" height="18" viewBox="0 0 16 18"><path d="M5 2 L12 9 L5 16" fill="none" stroke="#8cc63f" stroke-width="3"/></svg></div>
  <div class="hero-dots"><span class="on"></span><span></span><span></span><span></span></div>
</section>
<div class="hero-shadow"></div>

<section class="intro">
  <h2 class="heading">Social real estate investment</h2>
  <div class="rule"></div>
  <p>By harnessing the power of crowds, it's possible to become a landlord in locations around the world. Forget the burden of<br>financing <span class="accent">100%</span> of the purchase.</p>
  <p>Leave the day to day management of your property portfolio to us.</p>
  <p>Start with <span class="accent">1%</span> in a project and plan your steps to becoming a true baron</p>
</section>

<section class="join">
  <div class="join-card" style="left:202px">
    <div class="icon"><svg width="40" height="40" viewBox="0 0 40 40"><rect x="4" y="14" width="10" height="24" fill="#8cc63f"/><rect x="16" y="4" width="10" height="34" fill="#8cc63f"/><rect x="28" y="18" width="9" height="20" fill="#8cc63f"/></svg></div>
    <h3 class="heading">Find properties</h3>
    <p>Sign up to browse the portfolio.<br>Your journey to becoming a real<br>estate baron starts here.</p>
  </div>
  <div class="join-btn" style="left:202px">Become a member</div>
  <div class="join-card" style="left:628px">
    <div class="icon"><svg width="40" height="40" viewBox="0 0 40 40"><circle cx="10" cy="10" r="5" fill="#8cc63f"/><circle cx="30" cy="10" r="5" fill="#8cc63f"/><circle cx="20" cy="8" r="6" fill="#8cc63f"/><rect x="5" y="17" width="10" height="20" rx="3" fill="#8cc63f"/><rect x="25" y="17" width="10" height="20" rx="3" fill="#8cc63f"/><rect x="14" y="16" width="12" height="22" rx="3" fill="#8cc63f"/></svg></div>
    <h3 class="heading">Find Buyers</h3>
    <p>Submit a property or development<br>and raise funds from our real estate<br>barons.</p>
  </div>
  <div class="join-btn" style="left:628px">Submit a property</div>
</section>

<section class="projects">
  <h2 class="heading">Featured Projects</h2>
  <p class="lead">Brief details of new and popular projects. To view full listings, you will be required to<br>sign up and <span class="accent">become a member.</span></p>

  <article class="project raised" style="left:144px">
    <div class="project-photo" role="img" aria-label="Red brick family house with double garage"><span class="price-tag">From GBP 3,600</span><span class="launch-tag">New Launch</span></div>
    <h3>21 Quayside Lane LONDON E1</h3>
    <p class="summary">Lorem Ipsum is simply dummy text of the printing and typesetting industry. Lorem Ipsum has been the industry's...</p>
    <div class="funded">Funded<div class="bar"><div class="bar-fill" style="width:50%"></div><span class="bar-label" style="left:112px">50%</span></div></div>
    <div class="detail-link active">See Project Details</div>
  </article>

  <article class="project" style="left:456px">
    <div class="project-photo" role="img" aria-label="Cream and brick suburban house with garage"><span class="price-tag">From GBP 3,600</span><span class="launch-tag">New Launch</span></div>
    <h3>21 Quayside Lane LONDON E1</h3>
    <p class="summary">Lorem Ipsum is simply dummy text of the printing and typesetting industry. Lorem Ipsum has been the industry's...</p>
    <div class="funded">Funded<div class="bar"><div class="bar-fill" style="width:75%"></div><span class="bar-label" style="left:122px">75%</span></div></div>
    <div class="detail-link">See Project Details</div>
  </article>

  <article class="project" style="left:766px">
    <div class="project-photo" role="img" aria-label="White villa with terracotta roof among palm trees"><span class="price-tag">From GBP 3,600</span><span class="launch-tag">New Launch</span></div>
    <h3>21 Quayside Lane LONDON E1</h3>
    <p class="summary">Lorem Ipsum is simply dummy text of the printing and typesetting industry. Lorem Ipsum has been the industry's...</p>
    <div class="funded">Funded<div class="bar"><div class="bar-fill" style="width:40%"></div><span class="bar-label" style="left:124px">40%</span></div></div>
    <div class="detail-link">See Project Details</div>
  </article>
</section>

<section class="community" role="img" aria-label="Dark aerial view of a city at dusk behind a faint world map">
  <h2 class="heading">Be Part of a Growing International Community</h2>
  <p class="lead">Gain access to new projects in world class cities and join our growing community of international landlords.</p>

  <div class="stat" style="left:170px">
    <svg class="pin" style="left:14px;top:-12px" width="14" height="20" viewBox="0 0 14 20"><path d="M7 0a7 7 0 0 1 7 7c0 5-7 13-7 13S0 12 0 7a7 7 0 0 1 7-7z" fill="#8cc63f"/><circle cx="7" cy="7" r="2.5" fill="#2f2f2f"/></svg>
    <svg class="pin" style="left:70px;top:50px" width="10" height="14" viewBox="0 0 14 20"><path d="M7 0a7 7 0 0 1 7 7c0 5-7 13-7 13S0 12 0 7a7 7 0 0 1 7-7z" fill="#8cc63f"/></svg>
    <div class="figure">3,200 barons<br>in 6 countries</div>
    <p>A community of international<br>property barons.</p>
  </div>

  <div class="stat" style="left:466px">
    <svg class="pin" style="left:104px;top:-34px" width="52" height="40" viewBox="0 0 52 40"><circle cx="12" cy="10" r="6" fill="#666"/><circle cx="40" cy="10" r="6" fill="#666"/><circle cx="26" cy="8" r="8" fill="#777"/><rect x="4" y="18" width="16" height="20" rx="6" fill="#666"/><rect x="32" y="18" width="16" height="20" rx="6" fill="#666"/><rect x="16" y="18" width="20" height="22" rx="7" fill="#777"/></svg>
    <div class="figure">USD$ 16.2 million</div>
    <p>Collective buying power of<br>the pennyduke community</p>
  </div>

  <div class="stat" style="left:776px">
    <svg class="pin" style="left:20px;top:-16px" width="14" height="20" viewBox="0 0 14 20"><path d="M7 0a7 7 0 0 1 7 7c0 5-7 13-7 13S0 12 0 7a7 7 0 0 1 7-7z" fill="#8cc63f"/><circle cx="7" cy="7" r="2.5" fill="#2f2f2f"/></svg>
    <svg class="pin" style="left:220px;top:36px" width="10" height="14" viewBox="0 0 14 20"><path d="M7 0a7 7 0 0 1 7 7c0 5-7 13-7 13S0 12 0 7a7 7 0 0 1 7-7z" fill="#8cc63f"/></svg>
    <div class="figure">64 proposals in 6<br>countries</div>
    <p>Attractive real estate from<br>around the world</p>
  </div>
</section>

<section class="press" aria-label="Media partners">
  <div class="press-label">Featured In</div>
  <div class="press-row" style="left:36px;top:60px;gap:44px">
    <span class="press-badge" style="width:112px;height:22px"></span>
    <span class="press-badge" style="width:160px;height:20px"></span>
    <span class="press-badge" style="width:120px;height:26px"></span>
    <span class="press-badge" style="width:336px;height:20px"></span>
  </div>
  <div class="press-row" style="left:156px;top:118px;gap:36px">
    <span class="press-badge" style="width:62px;height:30px"></span>
    <span class="press-badge" style="width:128px;height:16px"></span>
    <span class="press-badge" style="width:40px;height:36px"></span>
    <span class="press-badge" style="width:70px;height:40px"></span>
    <span class="press-badge" style="width:140px;height:26px;border-radius:13px"></span>
  </div>
</section>

<div class="skyline" role="img" aria-label="Grey silhouette of world landmarks and city skylines"></div>

<footer>
  <div class="footer-bar">
    <div class="footer-follow">Follow us on
      <span class="footer-sq"><svg width="16" height="16" viewBox="0 0 16 16"><circle cx="4" cy="8" r="2.2" fill="#8cc63f"/><circle cx="12" cy="3.5" r="2.2" fill="#8cc63f"/><circle cx="12" cy="12.5" r="2.2" fill="#8cc63f"/><path d="M4 8 L12 3.5 M4 8 L12 12.5" stroke="#8cc63f" stroke-width="1.4"/></svg></span>
      <span class="footer-sq"><svg width="16" height="14" viewBox="0 0 16 14"><path d="M1 1h14v9H6l-4 3v-3H1z" fill="#8cc63f"/></svg></span>
    </div>
    <div class="copyright">© pennyduke 2014</div>
  </div>
  <div class="legal">
    <p style="top:22px;width:560px"><span class="accent">Penny Duke</span> is part of the Climb VC Group. The Climb VC Group is a worldwide pioneer and leader in the crowd investing, peer to peer and online investment market.</p>
    <p style="top:96px">By accessing this site and any pages thereof, you agree to be bound by the terms and conditions. This website is only suitable, intended and available for professional or sophisticated, or similar investors in other jurisdictions, or those who are members of pennyduke community and familiar with, and willing to, accept the risks associated with private participation. Pennyduke does not endorse any of the projects that appear on this website, nor does it make any recommendations regarding the appropriateness of particular opportunities for any participant. Each potential participant must review and evaluate the projects in his or her own discretion and determine the suitability of participating.</p>
    <p style="top:230px">This website (the "Site") is in every respect unaffiliated with any site to which it links or to any company or entity (and connected projects, investment opportunity or similar) featured on this Site, and is not meant as an endorsement of any of those companies or entities ("third parties"). Furthermore and for the avoidance of doubt, Pennyduke Limited is in no way affiliated with any third parties featured or referenced on this Site. There is no commercial relationship between Pennyduke Limited and such third parties, nor an agency arrangement or similar. If you believe your Content (including third party content) as each such term is defined in our Terms of Service has been reproduced on the Site without permission, please refer to our Terms of Service for information on how to request its removal from the Site.</p>
  </div>
  <div class="group-name">climb vc group</div>
</footer>

</body>
</html>
```